Australian Trucking Company Requires Professional Looking Stationary

We require a professional looking stationary design that incorporates our newly designed logo.

Our business, called "Brell Haulage Contracting", provides contracting work, transport and logistics to business in Western Australia particularly with links to the mining sector.

We are a small business looking to expand and our new logo and our new stationary will help develop our brand image in our market place.

Target Market(s)

Businesses and Corporation with links to the Mining Sector

Industry/Entity Type

Small Business

Requirements
Must have
• The letterhead must have the following details:
The new logo

Text saying: "Brell Holdings Pty Ltd (ACN 582 316 907) ATF The Brell Discretionary Trust T/AS"
"ABN 71 834 209 553"
Address "P.O Box 817 Wattlegrove WA, 6958"
Phone: 08 9352 7140
Email: brellhaul@mailbox-example.com.au

The text on the letterhead should be editable as the details are likely to change in the near future. Provision should be made for a website address all though one isn't available at the moment.

The styling, layout and font text is entirely up to the designer.

```html
<!DOCTYPE html>
<html lang="en">
<head>
<meta charset="utf-8">
<title>Brell Haulage Contracting – Business Cards</title>
<link href="https://fonts.googleapis.com/css2?family=Roboto:wght@400;500;700&display=swap" rel="stylesheet">
<style>
  :root {
    --page: #d9d6d2;
    --card: #ffffff;
    --band: #231f20;
    --red: #b41f24;
    --text: #3a3a3a;
    --muted: #7a7a7a;
    --art-light: #b9b9b9;
    --art-dark: #4a4a4a;
  }
  html, body {
    margin: 0;
    padding: 0;
    width: 1200px;
    height: 1200px;
    overflow: hidden;
    background: var(--page);
    font-family: "Roboto", Arial, sans-serif;
  }
  .canvas { position: relative; width: 1200px; height: 1200px; }

  .card {
    position: absolute;
    width: 840px;
    height: 480px;
    background: var(--card);
    overflow: hidden;
    box-shadow: 0 6px 18px rgba(0,0,0,0.25);
  }
  .card--front { left: 84px; top: 78px; }
  .card--back  { left: 284px; top: 650px; }

  .band {
    position: absolute;
    left: 0; top: 0;
    width: 100%;
    height: 187px;
    background: var(--band);
  }
  .rule {
    position: absolute;
    left: 0;
    top: 191px;
    width: 100%;
    height: 4px;
    background: var(--red);
  }

  .truck-art {
    position: absolute;
    border-radius: 18px;
    background: linear-gradient(180deg, var(--art-light) 0%, var(--art-dark) 100%);
  }
  .card--front .truck-art {
    left: 90px;
    top: 14px;
    width: 196px;
    height: 160px;
  }
  .card--back .truck-art {
    left: 16px;
    top: 12px;
    width: 394px;
    height: 318px;
    border-radius: 28px;
  }

  .brand {
    position: absolute;
    left: 312px;
    top: 18px;
    margin: 0;
    color: var(--red);
    font-weight: 700;
    font-size: 56px;
    line-height: 50px;
    text-transform: uppercase;
    letter-spacing: 0;
  }

  .person {
    position: absolute;
    right: 460px;
    top: 282px;
    text-align: right;
  }
  .person__name {
    margin: 0;
    color: var(--red);
    font-weight: 500;
    font-size: 31px;
    line-height: 36px;
  }
  .person__title {
    margin: 2px 0 0;
    color: var(--red);
    font-size: 24px;
    letter-spacing: 2px;
    line-height: 30px;
  }
  .person__address {
    margin: 18px 0 0;
    color: var(--text);
    font-size: 21px;
    line-height: 28px;
    font-style: normal;
  }

  .divider {
    position: absolute;
    left: 404px;
    top: 274px;
    width: 1px;
    height: 148px;
    background: var(--red);
  }

  .contacts {
    position: absolute;
    left: 430px;
    top: 292px;
    margin: 0;
    padding: 0;
    list-style: none;
    color: var(--text);
    font-size: 21px;
  }
  .contacts li {
    display: flex;
    align-items: center;
    height: 32px;
  }
  .contacts svg { width: 16px; height: 16px; margin-right: 10px; flex: none; }

  .legal {
    position: absolute;
    left: 329px;
    top: 350px;
    margin: 0;
    color: var(--muted);
    font-size: 21.5px;
    line-height: 31px;
  }
  .web {
    position: absolute;
    left: 329px;
    top: 420px;
    margin: 0;
    color: var(--text);
    font-size: 29px;
    letter-spacing: 2px;
  }
  .web strong { color: var(--red); font-weight: 700; }
</style>
</head>
<body>
<main class="canvas">

  <section class="card card--front" aria-label="Business card front">
    <div class="band"></div>
    <div class="rule"></div>
    <div class="truck-art" role="img" aria-label="Grey illustration of a prime mover truck"></div>
    <h1 class="brand">Brell<br>Haulage<br>Contracting</h1>

    <div class="person">
      <p class="person__name">Your Name</p>
      <p class="person__title">Title</p>
      <address class="person__address">P.O Box 817<br>Wattlegrove WA, 6958</address>
    </div>

    <div class="divider"></div>

    <ul class="contacts">
      <li>
        <svg viewBox="0 0 16 16" aria-hidden="true"><circle cx="8" cy="8" r="7" fill="none" stroke="#b41f24" stroke-width="1.4"/><path d="M5.5 4.5c-.8 2.5.9 6 3.8 7l1.3-1.6-1.5-1-1 .7c-.9-.6-1.5-1.6-1.7-2.6l1-.6-.5-1.7z" fill="#b41f24"/></svg>
        08 9352 7140
      </li>
      <li>
        <svg viewBox="0 0 16 16" aria-hidden="true"><rect x="1" y="4" width="14" height="9" fill="#b41f24"/><path d="M1 4l7 5 7-5" fill="none" stroke="#fff" stroke-width="1.2"/></svg>
        brellhaul@mailbox-example.com.au
      </li>
      <li>
        <svg viewBox="0 0 16 16" aria-hidden="true"><g fill="none" stroke="#b41f24" stroke-width="1.2"><circle cx="8" cy="8" r="6.5"/><ellipse cx="8" cy="8" rx="3" ry="6.5"/><path d="M1.5 8h13M2.5 5h11M2.5 11h11"/></g></svg>
        www.brellhaulage.com
      </li>
      <li>ABN 71 834 209 553</li>
    </ul>
  </section>

  <section class="card card--back" aria-label="Business card back">
    <div class="band"></div>
    <div class="rule"></div>
    <div class="truck-art" role="img" aria-label="Large grey illustration of a prime mover truck"></div>
    <p class="legal">Brell Holdings Pty Ltd (ACN 582 316 907)<br>ATF The Brell Discretionary Trust T/AS</p>
    <p class="web">www.<strong>brellhaulage</strong>.com</p>
  </section>

</main>
</body>
</html>
```